Verlindo Magician

I want the business card for my business to give to people who watch that later I will be employed to show magic here is my website http://www.balsamomagicien.com/I want the interesting design , i am very opened for formal and informal, I watch a lot of design so don't stick to the common shape and form but i hope it can also be produced the thing to write on will be the same as in picture that i will upload , i also will upload the logo for you that so can be easy to useDenis CostilleMagicianMAGICIAN VERLINDO 17 rue des Tilleuls - 25000 BESANÇON contact@verlindoillusions.example tel. 0381 946 157 tel. 0674 219 503

```html
<!DOCTYPE html>
<html lang="en">
<head>
<meta charset="utf-8">
<title>Verlindo Magician – Business Card</title>
<link href="https://fonts.googleapis.com/css2?family=Montserrat:wght@300;400;600&display=swap" rel="stylesheet">
<style>
  :root {
    --stage: #e4e4e6;
    --card: #ffffff;
    --ink: #111111;
    --ink-soft: #2a2a2a;
    --red: #e3141b;
    --frame: #1a1a1a;
    --shadow: rgba(0,0,0,0.18);
  }
  * { box-sizing: border-box; margin: 0; padding: 0; }
  html, body {
    width: 1200px; height: 900px; overflow: hidden;
    background: var(--stage);
    font-family: "Montserrat", sans-serif;
    color: var(--ink);
  }
  .stage {
    position: relative; width: 1200px; height: 900px;
    display: flex; justify-content: center; align-items: center; gap: 90px;
  }
  .card {
    position: relative; width: 380px; height: 600px;
    background: var(--card); border-radius: 26px;
    box-shadow: 0 14px 34px var(--shadow);
    overflow: hidden;
  }

  /* Front */
  .card-front { display: flex; flex-direction: column; align-items: center; padding-top: 78px; }
  .portrait {
    width: 170px; height: 160px; border-radius: 6px;
    background: linear-gradient(160deg, #3a3a3a 0%, #0c0c0c 70%);
  }
  .brand-name {
    margin-top: 14px; font-weight: 400; font-size: 30px; letter-spacing: 1px;
    color: var(--ink-soft); display: flex; align-items: center; gap: 10px;
  }
  .brand-dot { width: 9px; height: 9px; border-radius: 50%; background: var(--red); }
  .details { align-self: stretch; padding: 34px 0 0 66px; }
  .person-name { font-weight: 600; font-size: 27px; letter-spacing: 1px; line-height: 1; }
  .person-role { font-weight: 300; font-size: 17px; letter-spacing: 1.5px; margin: 4px 0 0 112px; color: var(--ink-soft); }
  .address { display: flex; align-items: center; gap: 12px; margin-top: 30px; }
  .address svg { width: 22px; height: 30px; flex: none; }
  .address p { font-weight: 300; font-size: 16px; line-height: 1.05; letter-spacing: 0.6px; text-transform: uppercase; }
  .contact { margin-top: 30px; font-weight: 300; font-size: 12.5px; line-height: 1.55; letter-spacing: 0.6px; text-transform: uppercase; color: var(--ink-soft); }
  .contact .web { font-size: 14px; }

  /* Back */
  .card-back .frame {
    position: absolute; left: 30px; right: 30px; top: 30px; bottom: 30px;
    border: 1.5px solid var(--frame);
  }
  .card-back .figure {
    position: absolute; left: 96px; right: 96px; top: 90px; bottom: 90px;
    background: linear-gradient(135deg, #1a1a1a 0%, #000 45%, #f4f4f4 46%, #f4f4f4 54%, #000 55%, #1a1a1a 100%);
  }
  .suit { position: absolute; width: 34px; height: 34px; }
  .suit-spade { left: 100px; top: 44px; }
  .suit-diamond { left: 44px; top: 130px; width: 30px; height: 30px; }
  .suit-heart { right: 42px; bottom: 128px; }
  .suit-club { right: 100px; bottom: 44px; }
  .side-name {
    position: absolute; font-weight: 400; font-size: 20px; letter-spacing: 5px; color: var(--ink);
    white-space: nowrap; writing-mode: vertical-rl; line-height: 1;
  }
  .side-name-left { left: 49px; top: 190px; }
  .side-name-right { right: 49px; bottom: 190px; transform: rotate(180deg); }
</style>
</head>
<body>
<main class="stage">

  <section class="card card-front">
    <div class="portrait" role="img" aria-label="Black ink illustration of the magician holding a playing card"></div>
    <div class="brand-name"><span>VERLINDO</span><span class="brand-dot"></span></div>
    <div class="details">
      <h1 class="person-name">MARC RAVOULET</h1>
      <p class="person-role">MAGICIAN</p>
      <div class="address">
        <svg viewBox="0 0 22 30" aria-hidden="true">
          <path d="M11 1C5.5 1 1.5 5 1.5 10.3 1.5 17 11 27 11 27s9.5-10 9.5-16.7C20.5 5 16.5 1 11 1z" fill="var(--ink)"/>
          <circle cx="11" cy="10.3" r="3.6" fill="#fff"/>
        </svg>
        <p>17 rue des Tilleuls<br>25000 Besançon</p>
      </div>
      <div class="contact">
        <p>contact@verlindoillusions.example</p>
        <p>0381 946 157 / 0674 219 503</p>
        <p class="web">www.verlindoillusions.example</p>
      </div>
    </div>
  </section>

  <section class="card card-back">
    <div class="frame"></div>
    <div class="figure" role="img" aria-label="Mirrored playing-card style illustration of the magician holding cards"></div>

    <svg class="suit suit-spade" viewBox="0 0 34 34" aria-hidden="true">
      <path d="M17 2C12 9 3 13 3 20c0 4.5 5.5 7 11 3.5L12 32h10l-2-8.5C25.5 27 31 24.5 31 20 31 13 22 9 17 2z" fill="var(--ink)"/>
    </svg>
    <svg class="suit suit-diamond" viewBox="0 0 30 30" aria-hidden="true">
      <polygon points="15,1 29,15 15,29 1,15" fill="var(--red)"/>
    </svg>
    <svg class="suit suit-heart" viewBox="0 0 34 34" aria-hidden="true">
      <path d="M17 31C12 24 3 20 3 12 3 7 7 3 11 3c3 0 5 2 6 4 1-2 3-4 6-4 4 0 8 4 8 9 0 8-9 12-14 19z" fill="var(--red)"/>
    </svg>
    <svg class="suit suit-club" viewBox="0 0 34 34" aria-hidden="true">
      <g fill="var(--ink)">
        <circle cx="17" cy="9" r="7"/><circle cx="9" cy="19" r="7"/><circle cx="25" cy="19" r="7"/>
        <path d="M15 18h4l2 14H13z"/>
      </g>
    </svg>

    <span class="side-name side-name-left">VERLINDO</span>
    <span class="side-name side-name-right">VERLINDO</span>
  </section>

</main>
</body>
</html>
```